TK Homes - Stone Dorf Design

Looking for a double sides design, 1 side for my realestate and the other for home building. ( TK Homes on 1 side, Stone Dorf card on the other Side
Side 1 - Marek Tove ~ Vox Realty logo and Company ( the Property quarter )
Marek Tove
Marek@Marektove.example
IG - Marek_Bzq_Realtor
FB - marekt
Cell - 5558130467
3847 61 St Nw

Side 2
Marek Tove
5558130467
IG - Stonedorf_Bzq
Stonedorfdev@mailbox.example

Target Market(s)

Home buyers/ sellers

Industry/Entity Type

Home builders - Realestate

Contact Information for Business Card

Above

Requirements
Must have
• Black OR White background - my information -

```html
<!DOCTYPE html>
<html lang="en">
<head>
<meta charset="utf-8">
<title>TK Homes and Stone Dorf business cards</title>
<link rel="stylesheet" href="https://fonts.googleapis.com/css2?family=Tinos:wght@400;700&display=swap">
<style>
  :root {
    --page: #2a2a2e;
    --card: #1f1e23;
    --blue: #0f72c2;
    --red: #e04f43;
    --white: #f4f4f4;
    --serif: "Tinos", "Times New Roman", serif;
  }
  * { box-sizing: border-box; margin: 0; padding: 0; }
  html, body { width: 1200px; height: 780px; overflow: hidden; }
  body { background: var(--page); position: relative; font-family: var(--serif); }

  .card {
    position: absolute;
    width: 600px;
    height: 340px;
    background: var(--card);
    border-radius: 30px;
    border-left: 4px solid var(--red);
    border-bottom: 4px solid var(--red);
    overflow: hidden;
    box-shadow: 0 18px 40px rgba(0,0,0,.45);
  }
  .card--builder { left: 50px; top: 40px; }
  .card--realty { left: 550px; top: 400px; }

  .brand {
    position: absolute;
    left: 0; top: 0;
    width: 300px; height: 280px;
    display: flex; align-items: center; justify-content: center; gap: 12px;
  }
  .brand__mark { width: 22px; height: 22px; background: var(--red); }
  .brand__name { color: var(--blue); font-weight: 700; font-size: 44px; letter-spacing: .5px; }

  .divider {
    position: absolute;
    left: 300px; top: 60px;
    width: 2px; height: 170px;
    background: var(--white);
  }

  .details {
    position: absolute;
    left: 330px; top: 46px;
    color: var(--white);
  }
  .card--realty .details { top: 34px; }
  .person { font-weight: 700; font-size: 34px; line-height: 1; }
  .person__first { color: var(--blue); }
  .person__last { color: var(--red); }
  .role { font-weight: 700; font-size: 17px; margin: 4px 0 8px 10px; }
  .address { font-size: 16px; margin: 0 0 6px 18px; }
  .contacts { list-style: none; margin-left: 18px; }
  .contacts li { display: flex; align-items: center; gap: 8px; font-size: 15px; line-height: 21px; }
  .contacts svg { width: 13px; height: 13px; flex: none; }

  .band {
    position: absolute;
    bottom: 0; left: 0; width: 100%; height: 44px;
  }
  .band__red { position: absolute; left: 40px; bottom: 0; width: 330px; height: 20px; background: var(--red); }
  .band__mark { position: absolute; left: 386px; bottom: 4px; width: 20px; height: 20px; border: 2px solid var(--blue); }
  .band__blue { position: absolute; left: 420px; bottom: 18px; right: 0; height: 22px; background: var(--blue); }
</style>
</head>
<body>

<section class="card card--builder" aria-label="Stone Dorf card">
  <div class="brand">
    <span class="brand__mark"></span>
    <span class="brand__name">Stone Dorf</span>
  </div>
  <div class="divider"></div>
  <div class="details">
    <p class="person"><span class="person__first">Marek</span> <span class="person__last">Tove</span></p>
    <p class="role">Director</p>
    <ul class="contacts">
      <li><svg viewBox="0 0 16 16"><path d="M4 1l3 3-2 2c1 2 3 4 5 5l2-2 3 3-2 3C7 15 1 9 1 3z" fill="var(--red)"/></svg>5558130467</li>
      <li><svg viewBox="0 0 16 16"><circle cx="8" cy="8" r="6" fill="none" stroke="var(--red)" stroke-width="2"/></svg>Stonedorf_Bzq</li>
      <li><svg viewBox="0 0 16 16"><rect x="1" y="3" width="14" height="10" fill="var(--red)"/><path d="M1 3l7 6 7-6" fill="none" stroke="var(--card)" stroke-width="1.5"/></svg>Stonedorfdev@mailbox.example</li>
    </ul>
  </div>
  <div class="band">
    <span class="band__red"></span>
    <span class="band__mark"></span>
    <span class="band__blue"></span>
  </div>
</section>

<section class="card card--realty" aria-label="TK Homes card">
  <div class="brand">
    <span class="brand__name">TK Homes</span>
  </div>
  <div class="divider"></div>
  <div class="details">
    <p class="person"><span class="person__first">Marek</span> <span class="person__last">Tove</span></p>
    <p class="role">Director</p>
    <p class="address">3847 61 St Nw</p>
    <ul class="contacts">
      <li><svg viewBox="0 0 16 16"><path d="M4 1l3 3-2 2c1 2 3 4 5 5l2-2 3 3-2 3C7 15 1 9 1 3z" fill="var(--blue)"/></svg>5558130467</li>
      <li><svg viewBox="0 0 16 16"><circle cx="8" cy="8" r="7" fill="var(--blue)"/></svg>marekt</li>
      <li><svg viewBox="0 0 16 16"><circle cx="8" cy="8" r="6" fill="none" stroke="var(--blue)" stroke-width="2"/></svg>Marek_Bzq_Realtor</li>
      <li><svg viewBox="0 0 16 16"><rect x="1" y="3" width="14" height="10" fill="var(--blue)"/><path d="M1 3l7 6 7-6" fill="none" stroke="var(--card)" stroke-width="1.5"/></svg>Marek@Marektove.example</li>
      <li><svg viewBox="0 0 16 16"><g fill="none" stroke="var(--blue)" stroke-width="1.4"><circle cx="8" cy="8" r="6.5"/><ellipse cx="8" cy="8" rx="3" ry="6.5"/><path d="M1.5 8h13"/></g></svg>www.marektove.example</li>
    </ul>
  </div>
  <div class="band">
    <span class="band__red"></span>
    <span class="band__mark"></span>
    <span class="band__blue"></span>
  </div>
</section>

</body>
</html>
```